Kinesiology undergraduate program needs an infographic

We would like an infographic to creatively and succinctly inform students, faculty, staff, and others about our undergraduate values and competencies (perhaps also integrating our mission and vision). We would like to see a design that incorporates the definition of Kinesiology (the study of human movement) and the colors of our Westbrook State University at Harlan.

```html
<!DOCTYPE html>
<html lang="en">
<head>
<meta charset="utf-8">
<title>Kinesiology Undergraduate Program</title>
<link href="https://fonts.googleapis.com/css2?family=Arimo:wght@400&display=swap" rel="stylesheet">
<style>
  :root {
    --navy: #13294b;
    --navy-text: #1b2b4f;
    --orange: #e84c26;
    --green: #557d2c;
    --body-text: #5d6169;
    --halo: rgba(205, 207, 211, 0.55);
    --bg-edge: #e1e5ea;
    --bg-center: #ffffff;
  }
  * { box-sizing: border-box; margin: 0; padding: 0; }
  html, body { width: 677px; height: 1200px; overflow: hidden; }
  body {
    font-family: "Arimo", Arial, sans-serif;
    color: var(--navy-text);
    background: var(--bg-edge);
  }
  .infographic {
    position: relative;
    width: 677px;
    height: 1200px;
    background:
      radial-gradient(ellipse 55% 20% at 50% 8%, var(--bg-center), transparent 100%),
      radial-gradient(ellipse 55% 25% at 50% 97%, var(--bg-center), transparent 100%),
      radial-gradient(ellipse 40% 18% at 50% 70%, #f4f6f8, transparent 100%),
      var(--bg-edge);
    overflow: hidden;
  }
  .program-title {
    position: absolute;
    top: 36px; left: 0; width: 100%;
    text-align: center;
    font-size: 18.5px;
    font-weight: 400;
    line-height: 33px;
    letter-spacing: 0.2px;
  }
  .halo {
    position: absolute;
    border-radius: 50%;
    background: radial-gradient(circle, transparent 58%, var(--halo) 72%, transparent 78%);
  }
  .halo--mission { left: 40px; top: 148px; width: 224px; height: 224px; }
  .halo--values  { left: 398px; top: 138px; width: 244px; height: 244px; }
  .halo--vision  { left: 213px; top: 313px; width: 234px; height: 234px; }
  .pillars-art { position: absolute; top: 0; left: 0; }
  .pillar {
    position: absolute;
    text-align: center;
  }
  .pillar h2 {
    font-size: 19.5px;
    font-weight: 400;
    line-height: 1;
  }
  .pillar p {
    margin-top: 7px;
    font-size: 9px;
    line-height: 12px;
    color: var(--body-text);
  }
  .pillar--mission { left: 52px; width: 206px; top: 415px; }
  .pillar--mission h2 { color: var(--orange); }
  .pillar--values { left: 425px; width: 180px; top: 415px; }
  .pillar--values h2 { color: var(--green); }
  .pillar--vision { left: 221px; width: 220px; top: 584px; }
  .pillar--vision h2 { color: var(--navy-text); }
  .competencies-heading {
    position: absolute;
    top: 702px; left: 0; width: 100%;
    text-align: center;
    font-size: 25px;
    font-weight: 400;
  }
  .competency { position: absolute; }
  .competency h3 {
    display: inline-block;
    height: 29px;
    padding: 0 12px;
    border: 1px solid var(--navy-text);
    border-radius: 15px;
    font-size: 13.2px;
    font-weight: 400;
    line-height: 27px;
    letter-spacing: 0.2px;
    white-space: nowrap;
  }
  .competency ul {
    list-style: none;
    margin-top: 22px;
  }
  .competency li {
    font-size: 11px;
    line-height: 20.7px;
  }
  .competency--science { left: 62px; top: 788px; }
  .competency--science ul { padding-left: 12px; }
  .competency--thinking { left: 390px; top: 788px; }
  .competency--thinking ul { padding-left: 12px; }
  .competency--relations { left: 41px; top: 953px; }
  .competency--relations ul { padding-left: 33px; }
  .competency--growth { left: 390px; top: 953px; }
  .competency--growth ul { padding-left: 12px; }
</style>
</head>
<body>
<main class="infographic">
  <h1 class="program-title">KINESIOLOGY UNDERGRADUATE<br>PROGRAM</h1>

  <div class="halo halo--mission" role="img" aria-label="Soft ring ornament around the mission circle"></div>
  <div class="halo halo--values" role="img" aria-label="Soft ring ornament around the values circle"></div>
  <div class="halo halo--vision" role="img" aria-label="Soft ring ornament around the vision circle"></div>

  <svg class="pillars-art" width="677" height="560" viewBox="0 0 677 560" aria-hidden="true">
    <defs>
      <filter id="soft-shadow" x="-30%" y="-30%" width="160%" height="170%">
        <feDropShadow dx="0" dy="6" stdDeviation="7" flood-color="#000" flood-opacity="0.22"/>
      </filter>
    </defs>
    <g filter="url(#soft-shadow)">
      <circle cx="150" cy="258" r="72" fill="var(--orange)"/>
      <circle cx="518" cy="258" r="72" fill="var(--green)"/>
      <circle cx="329" cy="425" r="72" fill="var(--navy)"/>
    </g>
    <g fill="#ffffff" font-family="Arimo, Arial, sans-serif" font-size="25" text-anchor="middle">
      <text x="150" y="267">MISSION</text>
      <text x="518" y="267">VALUES</text>
      <text x="329" y="434">VISION</text>
    </g>
  </svg>

  <section class="pillar pillar--mission">
    <h2>MISSION</h2>
    <p>To empower undergraduate students to pursue<br>excellence through scientific discovery,<br>clinical practice, and health promotion.</p>
  </section>
  <section class="pillar pillar--values">
    <h2>VALUES</h2>
    <p>Student Success, Science, and Service</p>
  </section>
  <section class="pillar pillar--vision">
    <h2>VISION</h2>
    <p>WSUH Kinesiology graduates are leaders<br>who excel in careers that enhance the quality<br>of life of individuals and communities.</p>
  </section>

  <h2 class="competencies-heading">Our Graduates Will Be Competent In :</h2>

  <section class="competency competency--science">
    <h3>THE SCIENCE OF KINESIOLOGY</h3>
    <ul>
      <li>Foundational Concepts of Kinesiology</li>
      <li>Clinical Application</li>
      <li>Scientific Communication</li>
    </ul>
  </section>
  <section class="competency competency--thinking">
    <h3>THINKING AND REASONING</h3>
    <ul>
      <li>Critical Thinking</li>
      <li>Quantitative Reasoning</li>
      <li>Scientific Inquiry</li>
      <li>Concept Integration</li>
    </ul>
  </section>
  <section class="competency competency--relations">
    <h3>RELATIONSHIPS AND COMMUNICATION</h3>
    <ul>
      <li>Cultural Competence</li>
      <li>Professionalism</li>
      <li>Leadership and Teamwork</li>
      <li>Service Orientation/Citizenship</li>
    </ul>
  </section>
  <section class="competency competency--growth">
    <h3>INTRAPERSONAL GROWTH</h3>
    <ul>
      <li>Cultural Humility/Sensitivity</li>
      <li>Integrity</li>
      <li>Self-Directed</li>
      <li>Dependability</li>
      <li>Mission Oriented</li>
    </ul>
  </section>
</main>
</body>
</html>
```